8x8 Social Media Ad - Brant Summit Expo

Attention Real Estate Agents
Please join us for our
Quarterly Real Estate Training Expo
The 2nd Saturday of February, May, August and November
Our Next Training Expo is _________________________________
From 9 am to 1 pm
at
Halvorne Suites Millbrook Court
4817 Copper Willow Lane, Dunmere, MD 20588
Scheduled Speakers
9:00 am - Marcus Pellington - Orientation
9:30 am - Derrin Oakfield - Multiple Income Streams / Crest Program
10:00 am - Talia Brennick - Marketing though Social Media
10:45 am - Rex Dunmore - Generating Business through Ru-Plaza
11:30 am - Kemi Adeyoro - Real Estate Investing
12:15 pm - Gregor Tamsey - (Main Speaker) Training Topic TBA
For more information call Marcus Pellington at (240) 555-0183 or email mpellington@brantsummithomes.example

```html
<!DOCTYPE html>
<html lang="en">
<head>
<meta charset="utf-8">
<title>Brant Summit Expo – Carousel</title>
<link href="https://fonts.googleapis.com/css2?family=Barlow+Condensed:wght@600&family=Jost:wght@300;400;500&display=swap" rel="stylesheet">
<style>
  :root {
    --red: #fd3333;
    --cream: #fdf6e3;
    --teal: #1f8a86;
    --gold: #f0b429;
    --ink: #1a1a1a;
    --paper: #ffffff;
    --photo: #6f6a66;
  }
  * { box-sizing: border-box; margin: 0; padding: 0; }
  html, body { width: 1200px; height: 1200px; overflow: hidden; background: var(--paper); }
  .canvas { position: relative; width: 1200px; height: 1200px; font-family: "Jost", sans-serif; color: var(--cream); }
  .board-title { position: absolute; left: 77px; top: 38px; font-weight: 300; font-size: 30px; letter-spacing: 1px; color: var(--ink); }
  .slide { position: absolute; width: 360px; height: 360px; background: var(--red); overflow: hidden; }
  .slide > * { position: absolute; }
  .brand { right: 14px; top: 22px; display: flex; align-items: center; gap: 4px; font-weight: 500; font-size: 11px; letter-spacing: .5px; color: var(--cream); }
  .brand::before { content: ""; width: 8px; height: 8px; background: var(--cream); }
  .rule { height: 1.5px; background: var(--cream); left: 20px; right: 22px; }
  .headline { font-family: "Barlow Condensed", sans-serif; font-weight: 600; text-transform: uppercase; line-height: .95; color: var(--cream); }
  .body { font-size: 13.5px; line-height: 1.15; letter-spacing: .3px; }

  .attention .headline { left: 26px; top: 46px; font-size: 50px; line-height: .9; }
  .attention .rule { top: 241px; left: 24px; }
  .attention .body { left: 20px; top: 260px; }

  .join .body { left: 36px; top: 62px; }
  .join .rule-a { top: 84px; }
  .join .headline { left: 35px; top: 90px; font-size: 31px; }
  .join .rule-b { top: 152px; }
  .photo-round { left: 148px; top: 161px; width: 178px; height: 178px; border-radius: 50%; border: 3px solid var(--teal); background: radial-gradient(circle at 45% 40%, #f2f4f7, #c9d2dc 60%, #a9b3bd); }

  .date .body { left: 36px; top: 62px; }
  .date .rule-a { top: 112px; }
  .date .headline { left: 34px; top: 128px; font-size: 34px; }
  .date .rule-b { top: 196px; }
  .date .venue { left: 47px; top: 213px; line-height: 1.15; }

  .contact .body { left: 38px; }
  .contact .lead { top: 64px; }
  .contact .rule-a { top: 89px; }
  .contact .headline { left: 37px; top: 96px; font-size: 29px; text-transform: none; line-height: 1; }
  .contact .or { top: 170px; }
  .contact .email { left: 37px; top: 226px; font-family: "Barlow Condensed", sans-serif; font-weight: 600; font-size: 19.5px; }
  .contact .rule-b { top: 271px; }

  .speakers .headline { left: 35px; top: 62px; font-size: 36px; }
  .speakers .rule-a { top: 100px; left: 24px; }
  .sched { left: 20px; top: 112px; width: 320px; }
  .sched .cell { position: absolute; background: var(--cream); color: var(--ink); border-radius: 5px; font-size: 7.6px; line-height: 1.15; }
  .sched .head { height: 11px; font-weight: 500; font-size: 6.5px; padding: 2px 0 0; }
  .sched .time { left: 0; width: 56px; display: flex; align-items: center; justify-content: center; }
  .sched .item { left: 65px; width: 253px; padding: 4px 4px; }
  .sched .head.time { display: block; text-align: center; }
  .sched .head.item { padding-left: 18px; }
  .chev { position: absolute; color: var(--teal); font-size: 11px; font-weight: 500; letter-spacing: -2px; }
  .portrait { position: absolute; width: 50px; height: 50px; border-radius: 50%; border: 3px solid var(--teal); background: radial-gradient(circle at 50% 40%, #8a817a, var(--photo) 60%, #3d3a38); }

  .arrow { position: absolute; }
</style>
</head>
<body>
<main class="canvas">
  <h1 class="board-title">CAROUSEL SOCIAL MEDIA DESIGN</h1>

  <svg class="arrow" style="left:318px;top:118px" width="62" height="40" viewBox="0 0 62 40"><path d="M0 12h36V0l26 20-26 20V28H0z" fill="var(--gold)"/></svg>
  <svg class="arrow" style="left:700px;top:118px" width="62" height="40" viewBox="0 0 62 40"><path d="M0 12h36V0l26 20-26 20V28H0z" fill="var(--gold)"/></svg>
  <svg class="arrow" style="left:1115px;top:550px" width="40" height="62" viewBox="0 0 40 62"><path d="M12 0h16v36h12L20 62 0 36h12z" fill="var(--gold)"/></svg>
  <svg class="arrow" style="left:770px;top:572px" width="62" height="40" viewBox="0 0 62 40"><path d="M62 12H26V0L0 20l26 20V28h36z" fill="var(--gold)"/></svg>

  <section class="slide attention" style="left:40px;top:185px">
    <div class="brand">BRANT SUMMIT</div>
    <h2 class="headline">Attention<br>Real<br>Estate<br>Agents</h2>
    <div class="rule"></div>
    <p class="body">This is an urgent<br>invite not to be<br>missed</p>
  </section>

  <section class="slide join" style="left:420px;top:185px">
    <div class="brand">BRANT SUMMIT</div>
    <p class="body">Please join us for our</p>
    <div class="rule rule-a"></div>
    <h2 class="headline">Quarterly Real<br>Estate Training Expo</h2>
    <div class="rule rule-b"></div>
    <div class="photo-round" role="img" aria-label="Photo of a model house on blueprints with keys"></div>
  </section>

  <section class="slide date" style="left:800px;top:185px">
    <div class="brand">BRANT SUMMIT</div>
    <p class="body">The 2nd Saturday of February,<br>May, August and November</p>
    <div class="rule rule-a"></div>
    <h2 class="headline">Our Next Training<br>Expo is Aug 13,2023</h2>
    <div class="rule rule-b"></div>
    <p class="body venue">From 9 am to 1 pm<br>at<br>Halvorne Suites Millbrook<br>Court<br>4817 Copper Willow Lane,<br>Dunmere, MD 20588</p>
  </section>

  <section class="slide contact" style="left:420px;top:615px">
    <div class="brand">BRANT SUMMIT</div>
    <p class="body lead">For more information call</p>
    <div class="rule rule-a"></div>
    <h2 class="headline">Marcus Pellington at<br>(240) 555-0183</h2>
    <p class="body or">or email</p>
    <p class="email">mpellington@brantsummithomes.example</p>
    <div class="rule rule-b"></div>
  </section>

  <section class="slide speakers" style="left:800px;top:615px">
    <div class="brand">BRANT SUMMIT</div>
    <h2 class="headline">Scheduled Speakers</h2>
    <div class="rule rule-a"></div>
    <div class="sched">
      <div class="cell head time" style="top:0">Time</div>
      <div class="cell head item" style="top:0">Itinerary</div>

      <div class="cell time" style="top:20px;height:28px">9:00 AM</div>
      <div class="cell item" style="top:20px;height:28px">Marcus Pellington -<br>Orientation</div>
      <span class="chev" style="left:208px;top:27px">&gt;&gt;&gt;</span>
      <div class="portrait" role="img" aria-label="Portrait of Marcus Pellington" style="left:225px;top:9px"></div>

      <div class="cell time" style="top:53px;height:28px">9:30 AM</div>
      <div class="cell item" style="top:53px;height:28px">Derrin Oakfield - Multiple Income<br>Streams / Crest Program</div>
      <span class="chev" style="left:258px;top:57px">&gt;&gt;&gt;</span>
      <div class="portrait" role="img" aria-label="Portrait of Derrin Oakfield" style="left:278px;top:42px"></div>

      <div class="cell time" style="top:88px;height:28px">10:00 AM</div>
      <div class="cell item" style="top:88px;height:28px">Talia Brennick - Marketing<br>though Social Media</div>
      <span class="chev" style="left:208px;top:94px">&gt;&gt;&gt;</span>
      <div class="portrait" role="img" aria-label="Portrait of Talia Brennick" style="left:225px;top:77px"></div>

      <div class="cell time" style="top:123px;height:28px">10:45 AM</div>
      <div class="cell item" style="top:123px;height:28px">Rex Dunmore - Generating<br>Business through Ru-Plaza</div>
      <span class="chev" style="left:258px;top:123px">&gt;&gt;&gt;</span>
      <div class="portrait" role="img" aria-label="Portrait of Rex Dunmore" style="left:278px;top:107px"></div>

      <div class="cell time" style="top:156px;height:28px">11:30 AM</div>
      <div class="cell item" style="top:156px;height:28px">Kemi Adeyoro - Real Estate<br>Investing</div>
      <span class="chev" style="left:208px;top:162px">&gt;&gt;&gt;</span>
      <div class="portrait" role="img" aria-label="Portrait of Kemi Adeyoro" style="left:225px;top:144px"></div>

      <div class="cell time" style="top:189px;height:28px">12:15 PM</div>
      <div class="cell item" style="top:189px;height:28px">Gregor Tamsey - (Main Speaker)<br>Training Topic TBA</div>
      <span class="chev" style="left:258px;top:196px">&gt;&gt;&gt;</span>
      <div class="portrait" role="img" aria-label="Portrait of Gregor Tamsey" style="left:278px;top:176px"></div>
    </div>
  </section>
</main>
</body>
</html>
```